Kestrelway Financial Plans

I am looking for a complete resdesign of my small financial presentation. This is a Word Doc/PDF that I print off when meeting with people in private. I often present my "two pager" that I have been using for years and years. It tells them the basics of what I do, how I help people and foundational financial principles.

I have recently gone out on my own in business and have completely rebranded. This presentation is my most used tool, so it is the first of many things I would like to redo. I am hoping it will somehow coordinate with the colors of my business, not necessarily the EXACT same 3 colors everywhere, but have the design colors compliment.

I've uploaded all my logo designs, as well as the current "two-pager". I am not against it going to 3 pages if needed. As it will still land on 2 pages with duplex printing.

It has always been VERY simple. I am wanting it built into a more professional and design specific format, to show off my branding, without being over cluttered.

I am completely open to ANY graphics changes. Obviously some are very novice, the house on the last page has always been overly simplified.

```html
<!DOCTYPE html>
<html lang="en">
<head>
<meta charset="utf-8">
<title>Kestrelway Financial Plans – Client Two-Pager</title>
<link href="https://fonts.googleapis.com/css2?family=Inter:wght@400;500;700;800&display=swap" rel="stylesheet">
<style>
:root{
  --green:#00ab3f;
  --navy:#101c2e;
  --mint:#dcefdc;
  --mint-deep:#cfe8d1;
  --grey:#848b92;
  --stage:#a8a8a8;
  --white:#ffffff;
  --ink:#1d2530;
}
*{box-sizing:border-box;margin:0;padding:0}
html,body{width:1200px;height:842px;overflow:hidden}
body{background:var(--stage);font-family:"Inter",Arial,sans-serif;color:var(--ink);position:relative}
.page{position:absolute;top:36px;width:545px;height:771px;overflow:hidden}
.page--left{left:36px;background:var(--mint)}
.page--right{left:619px;background:var(--mint)}
.abs{position:absolute}

/* header */
.title-bar{left:48px;top:13px;width:400px;height:38px;background:var(--green);border-radius:8px;color:var(--white);font-weight:800;font-size:18.5px;padding-left:23px;line-height:38px}
.brand-disc{left:432px;top:-33px;width:112px;height:112px;border-radius:50%;background:var(--white)}
.brand{left:443px;top:20px;width:90px;text-align:center;color:var(--navy);font-weight:700}
.brand__name{font-size:13px;letter-spacing:.2px}
.brand__sub{font-size:5px;letter-spacing:.9px;margin-top:1px}

/* challenge sections */
.topic-art{left:44px;width:134px;height:118px;border-radius:50%;background:linear-gradient(160deg,#9aa39f,#b9d6bf)}
.topic{left:199px;font-weight:700;font-size:11.5px;color:var(--ink)}
.stat{font-size:7.7px;line-height:10px;color:var(--ink)}
.stat--a{left:217px;width:124px}
.stat--b{left:368px;width:134px}
.stat::before{content:"";position:absolute;left:-13px;top:0;border-left:5.5px solid transparent;border-right:5.5px solid transparent;border-bottom:10px solid var(--green)}
.source{font-size:7.6px;font-weight:700;line-height:10px;white-space:nowrap}
.source--a{left:218px}
.source--b{left:370px}

/* who we are */
.dark-wave{left:0;top:440px;width:545px;height:331px}
.who{left:48px;top:526px;color:var(--white);font-weight:800;font-size:16.5px;line-height:22.5px}
.service{width:80px;text-align:center;color:var(--white);font-size:6.8px;font-weight:700;line-height:10px}
.service__icon{display:block;margin:0 auto 2px;width:42px;height:42px;border-radius:50%;background:#153a2a}

/* how */
.how-panel{left:49px;top:632px;width:447px;height:150px;background:var(--green);border-radius:12px 12px 0 0}
.how-title{left:70px;top:648px;color:var(--white);font-weight:800;font-size:17px;line-height:20.5px}
.checks{left:220px;top:649px;list-style:none;color:var(--white);font-size:7.8px;line-height:11px}
.checks li{position:relative;padding-left:13px}
.checks li svg{position:absolute;left:0;top:2px}
.partners{left:70px;top:701px;display:grid;grid-template-columns:repeat(5,46px);gap:3px 5px}
.partner{height:16px;border-radius:5px;background:#c9e5f0}
.pie{left:348px;top:635px;width:130px;height:130px}

/* right page */
.rule-bar{left:48px;top:54px;width:449px;height:39px;background:var(--green);border-radius:10px;color:var(--white);text-align:center;font-weight:800;font-size:18.5px;line-height:39px}
.rate-card{left:51px;top:111px;width:443px;height:192px;background:var(--white);border-radius:12px;box-shadow:0 2px 6px rgba(0,0,0,.12)}
.rate-col{top:120px;width:101px;height:143px;background:var(--mint)}
.rate-col__head{display:flex;justify-content:space-between;padding:8px 5px 0}
.pill{height:17px;border-radius:9px;font-size:7.6px;font-weight:700;color:var(--white);line-height:17px;padding:0 8px}
.pill--age{background:var(--green)}
.pill--rate{background:var(--navy);padding:0 6px}
.rate-rows{margin-top:4px;font-size:8px;font-weight:700;line-height:14.4px}
.rate-rows div{display:flex;justify-content:space-between;padding:0 11px 0 14px}
.rate-caption{top:272px;width:101px;text-align:center;font-size:7.3px;font-weight:700;line-height:9px;color:var(--ink)}

.taxes-title{left:0;width:545px;top:366px;text-align:center;font-weight:800;font-size:18px;color:var(--navy)}
.tax-card{top:402px;width:104px;height:144px;background:var(--navy);border-radius:10px;color:var(--white);text-align:center}
.tax-card__head{margin:8px 8px 0;height:24px;background:var(--green);border-radius:8px;font-weight:700;font-size:10px;line-height:24px}
.tax-card__body{position:absolute;left:6px;right:6px;top:45px;font-size:7.6px;line-height:11px}
.tax-card__body p{margin-bottom:7px}
.tax-card__rule{position:absolute;left:8px;right:8px;top:118px;height:1px;background:#2d3a4d}
.tax-card__verdict{position:absolute;left:0;right:0;top:123px;color:var(--green);font-weight:700;font-size:10px}

.green-sweep{left:0;top:560px;width:545px;height:211px}
.focus-box{top:586px;width:214px;height:60px;border:4.5px solid var(--navy);border-radius:14px;background:var(--white);display:flex;align-items:center;justify-content:center;text-align:center;font-weight:700;font-size:11.3px;line-height:17.5px;color:var(--navy)}
</style>
</head>
<body>

<!-- ===== Page 1: The Financial Challenge ===== -->
<section class="page page--left">
  <div class="abs title-bar">THE FINANCIAL CHALLENGE</div>
  <div class="abs brand-disc"></div>
  <div class="abs brand"><div class="brand__name">KESTRELWAY</div><div class="brand__sub">FINANCIAL PLANS</div></div>

  <!-- Savings -->
  <div class="abs topic-art" style="top:62px" role="img" aria-label="Savings emblem: ring with hand holding a dollar coin"></div>
  <div class="abs topic" style="top:76px">SAVINGS</div>
  <p class="abs stat stat--a" style="top:100px">49% of canadian employees are living paycheque to paycheque. 25% of Canadians are unable to cover an unexpected $500 expense</p>
  <p class="abs source source--a" style="top:156px">- STATS BUREAU (FEB 2023)</p>
  <p class="abs stat stat--b" style="top:100px">25% of canadians need to access their retirement savings early. 20% of Canadians have no savings. 39% of canadians aged 55-65 have less Than $5,000 in savings.</p>
  <p class="abs source source--b" style="top:156px">- FEDERAL FINANCE OFFICE<br>&nbsp;&nbsp;(JUNE 2023)</p>

  <!-- Debt -->
  <div class="abs topic-art" style="top:185px" role="img" aria-label="Debt emblem: ring with coin stack and percent sign"></div>
  <div class="abs topic" style="top:199px">DEBT</div>
  <p class="abs stat stat--a" style="top:223px">The average canadian has $22,131 in consumer debt. Which excludes Mortgages.</p>
  <p class="abs source source--a" style="top:280px">- CREDITLINE DATA (AUG 2024)</p>
  <p class="abs stat stat--b" style="top:223px">Over 55% of canadians hold credit card debt and the total canadian Household debt has increased to $2.52trillion, including consumer Credit, mortgage and non-mortgage</p>
  <p class="abs source source--b" style="top:280px">- NATIONAL LENDERS ASSOC.<br>(AUG 2024)</p>

  <!-- Insurance -->
  <div class="abs topic-art" style="top:310px" role="img" aria-label="Insurance emblem: ring with policy document and shield"></div>
  <div class="abs topic" style="top:324px">INSURANCE</div>
  <p class="abs stat stat--a" style="top:348px">45% of canadians do not have individual life insurance coverage, but 48% say their families would face financial trouble within 6 months of Losing someone.</p>
  <p class="abs source source--a" style="top:405px">-LIFEMARK INTL. (APR 2023)</p>
  <p class="abs stat stat--b" style="top:348px">2-in-5 canadians (43% women / 44% men) will be diagosed with a form of Cancer or other critical illness during their lifetime. Every 7 seconds.</p>
  <p class="abs source source--b" style="top:405px">-HEALTH DATAHUB CANADA<br>(JUNE 2024)</p>

  <!-- Who are we -->
  <svg class="abs dark-wave" viewBox="0 0 545 331" preserveAspectRatio="none">
    <path d="M0 82 Q270 -35 545 76 L545 331 L0 331 Z" fill="var(--green)"/>
    <path d="M0 98 Q270 -18 545 93 L545 331 L0 331 Z" fill="var(--navy)"/>
  </svg>
  <h2 class="abs who">WHO ARE WE AND<br>WHAT DO WE DO?</h2>

  <div class="abs service" style="left:227px;top:500px"><span class="service__icon" role="img" aria-label="Cash flow icon"></span>CASH FLOW</div>
  <div class="abs service" style="left:319px;top:500px"><span class="service__icon" role="img" aria-label="Cash flow protection icon"></span>CASH FLOW<br>PROTECTION</div>
  <div class="abs service" style="left:410px;top:500px"><span class="service__icon" role="img" aria-label="Debt management icon"></span>DEBT<br>MANAGEMENT</div>
  <div class="abs service" style="left:227px;top:562px"><span class="service__icon" role="img" aria-label="Emergency fund jar icon"></span>EMERGENCY<br>FUND</div>
  <div class="abs service" style="left:319px;top:562px"><span class="service__icon" role="img" aria-label="Piggy bank icon"></span>BUILD WEALTH</div>
  <div class="abs service" style="left:410px;top:562px"><span class="service__icon" role="img" aria-label="Preserve archive icon"></span>PRESERVE</div>

  <!-- How -->
  <div class="abs how-panel"></div>
  <h2 class="abs how-title">HOW ARE WE<br>DOING IT?</h2>
  <ul class="abs checks">
    <li><svg width="8" height="8" viewBox="0 0 8 8"><rect x=".5" y=".5" width="7" height="7" rx="1" fill="none" stroke="#fff"/><path d="M1.8 4 L3.4 5.6 L6.6 2" fill="none" stroke="#fff" stroke-width="1.1"/></svg>Retirement Savings</li>
    <li><svg width="8" height="8" viewBox="0 0 8 8"><rect x=".5" y=".5" width="7" height="7" rx="1" fill="none" stroke="#fff"/><path d="M1.8 4 L3.4 5.6 L6.6 2" fill="none" stroke="#fff" stroke-width="1.1"/></svg>Children’s Education</li>
    <li><svg width="8" height="8" viewBox="0 0 8 8"><rect x=".5" y=".5" width="7" height="7" rx="1" fill="none" stroke="#fff"/><path d="M1.8 4 L3.4 5.6 L6.6 2" fill="none" stroke="#fff" stroke-width="1.1"/></svg>Proper Protection</li>
    <li><svg width="8" height="8" viewBox="0 0 8 8"><rect x=".5" y=".5" width="7" height="7" rx="1" fill="none" stroke="#fff"/><path d="M1.8 4 L3.4 5.6 L6.6 2" fill="none" stroke="#fff" stroke-width="1.1"/></svg>Freedom From DEBT</li>
  </ul>
  <div class="abs partners" aria-label="Partner carriers">
    <span class="partner"></span><span class="partner"></span><span class="partner"></span><span class="partner"></span><span class="partner"></span>
    <span class="partner"></span><span class="partner"></span><span class="partner"></span><span class="partner"></span><span class="partner"></span>
  </div>
  <svg class="abs pie" viewBox="0 0 130 130" font-family="Inter, Arial, sans-serif" font-weight="700">
    <circle cx="60" cy="73" r="55" fill="var(--navy)"/>
    <line x1="60" y1="18" x2="60" y2="128" stroke="#fff" stroke-width="2"/>
    <line x1="60" y1="73" x2="112" y2="52" stroke="#fff" stroke-width="2"/>
    <line x1="58" y1="70" x2="25" y2="10" stroke="#bbb" stroke-width=".6"/>
    <text x="6" y="8" fill="#fff" font-size="7.8">Savings</text>
    <text x="68" y="51" fill="#fff" font-size="6.4">Taxes</text>
    <text x="16" y="68" fill="#fff" font-size="6.4">Living</text>
    <text x="16" y="78" fill="#fff" font-size="6.4">Expenses</text>
    <text x="66" y="98" fill="#fff" font-size="6.4">Debt</text>
  </svg>
</section>

<!-- ===== Page 2: Rule of 72 & Taxes ===== -->
<section class="page page--right">
  <svg class="abs" style="left:0;top:0" width="545" height="320" viewBox="0 0 545 320">
    <path d="M0 210 Q272 360 545 210 L545 240 Q272 395 0 240 Z" fill="var(--green)"/>
    <path d="M0 0 H545 V212 Q272 362 0 212 Z" fill="var(--navy)"/>
  </svg>

  <div class="abs rule-bar">RULE OF 72</div>
  <div class="abs rate-card"></div>

  <div class="abs rate-col" style="left:62px">
    <div class="rate-col__head"><span class="pill pill--age">Age</span><span class="pill pill--rate">4%</span></div>
    <div class="rate-rows"><div><span>29</span><span>$10,000</span></div><div><span>47</span><span>$20,000</span></div><div><span>65</span><span>$40,000</span></div></div>
  </div>
  <div class="abs rate-col" style="left:169px">
    <div class="rate-col__head"><span class="pill pill--age">Age</span><span class="pill pill--rate">6%</span></div>
    <div class="rate-rows"><div><span>29</span><span>$10,000</span></div><div><span>41</span><span>$20,000</span></div><div><span>53</span><span>$40,000</span></div><div><span>65</span><span>$80,000</span></div></div>
  </div>
  <div class="abs rate-col" style="left:277px">
    <div class="rate-col__head"><span class="pill pill--age">Age</span><span class="pill pill--rate">8%</span></div>
    <div class="rate-rows"><div><span>29</span><span>$10,000</span></div><div><span>38</span><span>$20,000</span></div><div><span>47</span><span>$40,000</span></div><div><span>56</span><span>$80,000</span></div><div><span>65</span><span>$160,000</span></div></div>
  </div>
  <div class="abs rate-col" style="left:385px">
    <div class="rate-col__head"><span class="pill pill--age">Age</span><span class="pill pill--rate">12%</span></div>
    <div class="rate-rows"><div><span>29</span><span>$10,000</span></div><div><span>35</span><span>$20,000</span></div><div><span>41</span><span>$40,000</span></div><div><span>47</span><span>$80,000</span></div><div><span>53</span><span>$160,000</span></div><div><span>59</span><span>$320,000</span></div><div><span>65</span><span>$640,000</span></div></div>
  </div>
  <p class="abs rate-caption" style="left:62px">MONEY DOUBLES<br>EVERY 18 YEARS</p>
  <p class="abs rate-caption" style="left:169px">MONEY DOUBLES<br>EVERY 12 YEARS</p>
  <p class="abs rate-caption" style="left:277px">MONEY DOUBLES<br>EVERY 19 YEARS</p>
  <p class="abs rate-caption" style="left:385px">MONEY DOUBLES<br>EVERY 16 YEARS</p>

  <h2 class="abs taxes-title">TAXES</h2>

  <div class="abs tax-card" style="left:48px">
    <div class="tax-card__head">HOME</div>
    <div class="tax-card__body"><p>Partnerwith mortgage brokers for best rates</p><p style="margin-top:11px">Mortgage insurance alternatives</p></div>
    <div class="tax-card__rule"></div><div class="tax-card__verdict">Sell</div>
  </div>
  <div class="abs tax-card" style="left:162px">
    <div class="tax-card__head">RRSP</div>
    <div class="tax-card__body"><p>Tax deduction</p><p style="margin-top:33px">Tax deferred</p></div>
    <div class="tax-card__rule"></div><div class="tax-card__verdict">100% Tax</div>
  </div>
  <div class="abs tax-card" style="left:277px">
    <div class="tax-card__head">TFSA</div>
    <div class="tax-card__body"><p>No tax deduction</p><p>No tax deductions</p><p>2009- $95,000</p><p>Limit 2023-$7,000/yr</p></div>
    <div class="tax-card__rule"></div><div class="tax-card__verdict">0%Tax</div>
  </div>
  <div class="abs tax-card" style="left:391px">
    <div class="tax-card__head">PERM LIFE</div>
    <div class="tax-card__body"><p>No tax deductions</p><p>Qualify</p><p>Tax deferred growth</p></div>
    <div class="tax-card__rule"></div><div class="tax-card__verdict">0%Tax</div>
  </div>

  <svg class="abs green-sweep" viewBox="0 0 545 211" preserveAspectRatio="none">
    <path d="M40 211 Q260 90 545 55 L545 211 Z" fill="var(--white)"/>
    <path d="M60 211 Q280 98 545 62 L545 211 Z" fill="var(--green)"/>
  </svg>

  <div class="abs focus-box" style="left:46px">LIFE INSURANCE ILLNESS<br>CRITICAL/ DISABILITY</div>
  <div class="abs focus-box" style="left:284px">DEBT MANAGEMENT<br>CASH FLOW</div>
</section>

</body>
</html>
```